NEW Modern Sleek Business Card for VR Language Startup

Our startup is using VR to lead the next wave of world language education. We need a two-sided business card that introduces the larger organization (Brightloom Language Inc) and our contact info on one side and shows the product, Glimwoorld, on the other side.

Side 1 (contact info)= Brightloom Logo and Contact info (name, title, phone, email)

Side 2 (product)= Glimworld logo, text, and website
Text= Culturally Immersive Language Learning Games
Website= www.glimworld-play.com

Target Market(s)

Education, Technology

Contact Information for Business Card

Contact info will be updated upon approval of the design. For now, put this as a placeholder.

Perry Dunmore
Founder & CEO
pdunmore@quillpost-mail.net
(555)-014-2286

Font styles to use
Other font styles liked:
• Gibson and Century Gothic are the brand fonts

Requirements
Nice to have
• I would love to see cohesion between the design and colors of the two logos. I have attached a few business card designs that I like, so you can get a feel for my preferred style.

```html
<!DOCTYPE html>
<html lang="en">
<head>
<meta charset="utf-8">
<title>Brightloom Language – Business Card</title>
<link rel="stylesheet" href="https://fonts.googleapis.com/css2?family=Montserrat:wght@400;600;700&family=Questrial&display=swap">
<style>
  :root {
    --backdrop: #3a3a3c;
    --white: #ffffff;
    --ink: #4a4a4c;
    --ink-soft: #555558;
    --orange: #f8b23a;
    --red: #ee2f46;
    --magenta: #a2318f;
    --violet: #7466ab;
    --cyan: #4fcbd9;
    --sky: #33c3ef;
    --indigo: #6a5ca8;
    --brand-gradient: linear-gradient(to bottom right, var(--orange) 0%, var(--red) 30%, var(--magenta) 50%, var(--violet) 68%, var(--cyan) 95%);
  }
  * { box-sizing: border-box; margin: 0; padding: 0; }
  html, body {
    width: 984px; height: 1200px; overflow: hidden;
    background: var(--backdrop);
  }
  .card {
    position: absolute;
    left: 171px;
    width: 642px; height: 416px;
    border-radius: 32px;
    overflow: hidden;
  }
  /* Front */
  .card--contact {
    top: 158px;
    background: var(--brand-gradient);
    color: var(--white);
  }
  .contact-header {
    position: absolute; top: 34px; left: 0; right: 0;
    display: flex; justify-content: center; align-items: baseline; gap: 26px;
  }
  .person-name {
    font-family: "Montserrat", sans-serif; font-weight: 700;
    font-size: 19px; letter-spacing: 10px;
  }
  .person-title {
    font-family: "Questrial", sans-serif;
    font-size: 14px; letter-spacing: 6px;
  }
  .company-mark {
    position: absolute; top: 150px; left: 0; right: 0;
    display: flex; justify-content: center; align-items: center; gap: 22px;
  }
  .company-mark__dot {
    width: 84px; height: 84px; border-radius: 50%;
    background: var(--white);
  }
  .company-mark__name {
    font-family: "Montserrat", sans-serif; font-weight: 700;
    color: var(--white); line-height: 1;
  }
  .company-mark__name span { display: block; }
  .company-mark__name .line-main { font-size: 42px; letter-spacing: 4px; }
  .company-mark__name .line-sub { font-size: 22px; letter-spacing: 12.5px; margin-top: 10px; padding-left: 12px; }
  .contact-row {
    position: absolute; top: 364px; left: 28px; right: 28px;
    display: flex; justify-content: space-between; align-items: center;
    font-family: "Questrial", sans-serif; font-size: 15px; letter-spacing: 3.2px;
  }
  .contact-item { display: flex; align-items: center; gap: 14px; }
  .contact-icon { width: 25px; height: 25px; flex: none; }
  /* Back */
  .card--product {
    top: 626px;
    background: var(--white);
  }
  .wave { position: absolute; inset: 0; width: 642px; height: 416px; }
  .product-mark {
    position: absolute; top: 118px; left: 0; right: 0;
    display: flex; flex-direction: column; align-items: center;
  }
  .product-mark__dot {
    width: 104px; height: 104px; border-radius: 50%;
    background: var(--sky);
  }
  .product-mark__name {
    margin-top: 14px;
    font-family: "Montserrat", sans-serif; font-weight: 600;
    font-size: 38px; line-height: 1; color: var(--ink);
  }
  .tagline {
    position: absolute; top: 296px; left: 0; right: 0;
    text-align: center;
    font-family: "Questrial", sans-serif; font-size: 14px; line-height: 21px;
    letter-spacing: 6.4px; color: var(--ink-soft);
  }
  .divider {
    position: absolute; top: 357px; left: 152px; width: 340px; height: 2px;
    background: linear-gradient(to right, var(--cyan), var(--indigo));
  }
  .website {
    position: absolute; top: 372px; left: 154px;
    display: flex; align-items: center; gap: 18px;
    font-family: "Questrial", sans-serif; font-size: 16px; letter-spacing: 5.4px;
    color: var(--ink);
  }
  .website .contact-icon { width: 25px; height: 25px; }
</style>
</head>
<body>

<section class="card card--contact" aria-label="Business card front">
  <header class="contact-header">
    <span class="person-name">PERRY DUNMORE</span>
    <span class="person-title">FOUNDER &amp; CEO</span>
  </header>

  <div class="company-mark">
    <div class="company-mark__dot"></div>
    <div class="company-mark__name">
      <span class="line-main">BRIGHTLOOM</span>
      <span class="line-sub">LANGUAGE</span>
    </div>
  </div>

  <div class="contact-row">
    <div class="contact-item">
      <svg class="contact-icon" viewBox="0 0 24 24" aria-hidden="true">
        <circle cx="12" cy="12" r="12" fill="#fff"/>
        <rect x="5.5" y="7.5" width="13" height="9" rx="1" fill="none" stroke="#c4307a" stroke-width="1.4"/>
        <path d="M5.5 8 L12 13 L18.5 8 M5.5 16.5 L10 12 M18.5 16.5 L14 12" fill="none" stroke="#c4307a" stroke-width="1.2"/>
      </svg>
      <span>pdunmore@quillpost-mail.net</span>
    </div>
    <div class="contact-item">
      <svg class="contact-icon" viewBox="0 0 24 24" aria-hidden="true">
        <circle cx="12" cy="12" r="12" fill="#fff"/>
        <path d="M8.2 6.2 L10 8.6 L9 10.2 C9.8 12 11.6 13.8 13.6 14.8 L15.2 13.8 L17.6 15.6 L16.6 17.6 C12 17.8 6.4 12.2 6.4 7.4 Z" fill="none" stroke="#8a5aa8" stroke-width="1.3" stroke-linejoin="round"/>
      </svg>
      <span>(555)-014-2286</span>
    </div>
  </div>
</section>

<section class="card card--product" aria-label="Business card back">
  <svg class="wave" viewBox="0 0 642 416" aria-hidden="true">
    <defs>
      <linearGradient id="waveGradient" gradientUnits="userSpaceOnUse" x1="0" y1="0" x2="560" y2="330">
        <stop offset="0" stop-color="#f8b23a"/>
        <stop offset="0.3" stop-color="#ee2f46"/>
        <stop offset="0.5" stop-color="#a2318f"/>
        <stop offset="0.68" stop-color="#7466ab"/>
        <stop offset="0.95" stop-color="#4fcbd9"/>
      </linearGradient>
    </defs>
    <path d="M0 0 H642 V129 C600 60 540 40 475 40 C400 40 360 58 322 80 C240 122 140 175 60 169 C30 167 12 160 0 154 Z" fill="url(#waveGradient)"/>
  </svg>

  <div class="product-mark">
    <div class="product-mark__dot"></div>
    <div class="product-mark__name">Glimworld</div>
  </div>

  <p class="tagline">CULTURALLY IMMERSIVE<br>LANGUAGE LEARNING GAMES</p>

  <div class="divider"></div>

  <div class="website">
    <svg class="contact-icon" viewBox="0 0 24 24" aria-hidden="true">
      <circle cx="12" cy="12" r="12" fill="#4a4a4c"/>
      <g fill="none" stroke="#fff" stroke-width="1">
        <circle cx="12" cy="12" r="6.5"/>
        <ellipse cx="12" cy="12" rx="3" ry="6.5"/>
        <path d="M5.5 12 H18.5 M6.5 8.8 H17.5 M6.5 15.2 H17.5 M12 5.5 V18.5"/>
      </g>
    </svg>
    <span>www.glimworld-play.com</span>
  </div>
</section>

</body>
</html>
```